Business Card Design for company

We want new business cards. We'd like something different-- yet still highly professional. Our tagline is Guiding strategy, building lasting results. Stock photos are ok, as long as they are relevant and look upscale.

Target Market(s)

Architecture/Business Management Consulting/Engineering Consulting

Contact Information for Business Card

dark gray background with pops of blue might be good, but you tell me. You're the designers. Rounded corners might be nice, but again, you tell me.

Font styles to use
Serif
Sans Serif

Colors
3276b5
5c5c5c
9d9d9d
fbfbfb

Requirements
Nice to have
• Something different, but still very professional.

```html
<!DOCTYPE html>
<html lang="en">
<head>
<meta charset="UTF-8">
<title>Varen Advisory — Business Card</title>
<link rel="stylesheet" href="https://fonts.googleapis.com/css2?family=Montserrat:wght@400;500;600;700&display=swap">
<style>
  :root {
    --blue: #3276b5;
    --gray-dark: #5c5c5c;
    --gray-mid: #9d9d9d;
    --paper: #fbfbfb;
    --stage: #e6e7e9;
    --card-dark-1: #3a3a3a;
    --card-dark-2: #1c1c1c;
    --ink: #3d3d3d;
    --light-mark: #e9e9e9;
  }
  * { margin: 0; padding: 0; box-sizing: border-box; }
  html, body {
    width: 1200px; height: 900px; overflow: hidden;
    background: var(--stage);
    font-family: "Montserrat", sans-serif;
  }
  .canvas {
    width: 1200px; height: 900px;
    display: flex; flex-direction: column;
    align-items: center; justify-content: center; gap: 44px;
  }
  .card {
    position: relative;
    width: 660px; height: 377px;
    border-radius: 30px;
    overflow: hidden;
    box-shadow: 0 14px 34px rgba(0,0,0,0.18);
  }

  /* Front */
  .card-front {
    background: linear-gradient(160deg, #ffffff 0%, var(--paper) 55%, #eeeeee 100%);
  }
  .front-tab {
    position: absolute; left: 0; top: 62px;
    width: 10px; height: 30px;
    background: var(--blue);
    border-radius: 0 5px 5px 0;
  }
  .identity { position: absolute; left: 48px; top: 58px; }
  .person-name {
    font-weight: 700; font-size: 23px; letter-spacing: 1px;
    color: var(--blue); text-transform: uppercase; line-height: 1.1;
  }
  .person-title {
    font-weight: 500; font-size: 16px; color: var(--gray-dark);
    margin-top: 2px;
  }
  .name-rule {
    position: absolute; left: 265px; top: 96px;
    width: 300px; height: 1.5px; background: var(--blue);
  }
  .contact {
    position: absolute; left: 48px; top: 138px;
    font-size: 15px; font-weight: 500; color: var(--ink);
    line-height: 1.45;
  }
  .contact-row { display: flex; align-items: center; gap: 8px; }
  .contact-row svg { width: 13px; height: 13px; fill: var(--blue); flex: none; }
  .address { margin-bottom: 2px; }

  .brand-front {
    position: absolute; right: 48px; top: 170px;
    display: flex; align-items: center; gap: 12px;
  }
  .brand-mark { width: 26px; height: 26px; background: var(--blue); }
  .brand-name {
    font-weight: 600; font-size: 27px; letter-spacing: 2px;
    text-transform: uppercase; color: var(--gray-dark);
  }

  .website {
    position: absolute; right: 62px; bottom: 28px;
    font-size: 15px; font-weight: 500; color: var(--blue);
    letter-spacing: 0.3px;
  }
  .bottom-band {
    position: absolute; right: 0; bottom: 0;
    width: 300px; height: 14px;
    background: var(--blue);
    border-radius: 10px 0 0 0;
  }

  /* Back */
  .card-back {
    background: radial-gradient(ellipse at 35% 20%, var(--card-dark-1) 0%, #262626 55%, var(--card-dark-2) 100%);
    display: flex; flex-direction: column; align-items: center; justify-content: center;
    gap: 26px;
  }
  .brand-back { display: flex; align-items: center; gap: 16px; }
  .brand-back .brand-mark { width: 36px; height: 36px; background: var(--light-mark); }
  .brand-back .brand-name { color: var(--light-mark); font-size: 40px; letter-spacing: 3px; }
  .tagline {
    font-size: 17px; font-weight: 500; color: var(--blue); letter-spacing: 0.6px;
  }
</style>
</head>
<body>
  <main class="canvas">
    <section class="card card-front" aria-label="Business card front">
      <div class="front-tab"></div>
      <div class="identity">
        <p class="person-name">Daniel Hartwell</p>
        <p class="person-title">CEO &amp; Founder</p>
      </div>
      <div class="name-rule"></div>
      <div class="contact">
        <p class="address">2210 W. Elm Street Suite 410<br>Mesa, AZ 85201</p>
        <p class="contact-row">
          <svg viewBox="0 0 24 24" aria-hidden="true"><path d="M6.6 10.8a15.1 15.1 0 0 0 6.6 6.6l2.2-2.2a1 1 0 0 1 1-.25 11.4 11.4 0 0 0 3.6.57 1 1 0 0 1 1 1V20a1 1 0 0 1-1 1A17 17 0 0 1 3 4a1 1 0 0 1 1-1h3.5a1 1 0 0 1 1 1c0 1.25.2 2.450.57 3.57a1 1 0 0 1-.25 1z"/></svg>
          (555) 210.4417
        </p>
        <p class="contact-row">
          <svg viewBox="0 0 24 24" aria-hidden="true"><path d="M2 5h20v14H2zm2 2v.5l8 5 8-5V7zm0 2.8V17h16V9.8l-8 5z"/></svg>
          info@varenadvisory.com
        </p>
      </div>
      <div class="brand-front">
        <span class="brand-mark"></span>
        <span class="brand-name">Varen Advisory</span>
      </div>
      <p class="website">www.varenadvisory.com</p>
      <div class="bottom-band"></div>
    </section>

    <section class="card card-back" aria-label="Business card back">
      <div class="brand-back">
        <span class="brand-mark"></span>
        <span class="brand-name">Varen Advisory</span>
      </div>
      <p class="tagline">Guiding strategy, building lasting results</p>
    </section>
  </main>
</body>
</html>
```